NEW Modern Sleek Business Card for VR Language Startup

Our startup is using VR to lead the next wave of world language education. We need a two-sided business card that introduces the larger organization (Brightloom Language Inc) and our contact info on one side and shows the product, Glimwoorld, on the other side.

Side 1 (contact info)= Brightloom Logo and Contact info (name, title, phone, email)

Side 2 (product)= Glimworld logo, text, and website
Text= Culturally Immersive Language Learning Games
Website= www.glimworld-play.com

Target Market(s)

Education, Technology

Contact Information for Business Card

Contact info will be updated upon approval of the design. For now, put this as a placeholder.

Perry Dunmore
Founder & CEO
pdunmore@quillpost-mail.net
(555)-014-2286

Font styles to use
Other font styles liked:
• Gibson and Century Gothic are the brand fonts

Requirements
Nice to have
• I would love to see cohesion between the design and colors of the two logos. I have attached a few business card designs that I like, so you can get a feel for my preferred style.

```html
<!DOCTYPE html>
<html lang="en">
<head>
<meta charset="utf-8">
<title>Brightloom Language – Business Card</title>
<link rel="stylesheet" href="https://fonts.googleapis.com/css2?family=Roboto:wght@400;500;700&display=swap">
<style>
  :root {
    --bg: #d3d7d8;
    --card: #f7f7f5;
    --name-blue: #3a8fe0;
    --title-orange: #f28a2e;
    --ink: #3b3b3b;
    --rule: #8d8d8d;
    --brand-dark: #2a2a2a;
    --product-blue: #1f5fd6;
    --pattern-teal: #bfe9ec;
    --pattern-lilac: #c9cdf3;
    --edge-teal: #2aa7c6;
  }
  * { box-sizing: border-box; margin: 0; padding: 0; }
  html, body { width: 1200px; height: 824px; overflow: hidden; }
  body {
    background: var(--bg);
    font-family: "Roboto", Arial, sans-serif;
    display: flex;
    align-items: center;
    justify-content: center;
    gap: 40px;
  }
  .card {
    position: relative;
    width: 520px;
    height: 297px;
    background: var(--card);
    border-bottom: 4px solid var(--edge-teal);
    box-shadow: 0 10px 24px rgba(0,0,0,.14);
    overflow: hidden;
  }

  /* Contact side */
  .contact-name {
    position: absolute; left: 30px; top: 112px;
    font-size: 24px; font-weight: 500; color: var(--name-blue);
  }
  .contact-title {
    position: absolute; left: 30px; top: 142px;
    font-size: 15px; color: var(--title-orange);
  }
  .contact-rule {
    position: absolute; left: 30px; right: 26px; top: 170px;
    height: 1px; background: var(--rule);
  }
  .contact-list {
    position: absolute; left: 30px; top: 184px;
    list-style: none; font-size: 14px; color: var(--ink);
  }
  .contact-list li { display: flex; align-items: center; gap: 10px; margin-bottom: 6px; }
  .contact-list svg { width: 13px; height: 13px; fill: var(--ink); }
  .brand {
    position: absolute; right: 34px; top: 64px;
    display: flex; align-items: center; gap: 12px;
  }
  .brand-dot { width: 44px; height: 44px; border-radius: 50%; background: #7a4df0; }
  .brand-name { font-size: 30px; font-weight: 500; color: var(--brand-dark); letter-spacing: 1px; }

  /* Product side */
  .pattern-field {
    position: absolute; inset: 0;
    background: linear-gradient(135deg, var(--pattern-lilac), var(--pattern-teal) 50%, var(--pattern-lilac));
    opacity: .75;
  }
  .product-block {
    position: absolute; inset: 0;
    display: flex; flex-direction: column; align-items: center; justify-content: center;
  }
  .product-mark { display: flex; align-items: center; gap: 10px; }
  .product-dot { width: 34px; height: 34px; border-radius: 50%; background: var(--product-blue); }
  .product-name { font-size: 30px; font-weight: 500; color: var(--product-blue); }
  .product-tagline {
    margin-top: 8px; font-size: 12px; font-weight: 700; color: var(--brand-dark);
    font-style: italic;
  }
  .product-web { margin-top: 8px; display: flex; align-items: center; gap: 8px; }
  .product-web svg { width: 110px; height: 10px; }
  .product-url { font-size: 13px; color: var(--product-blue); }
</style>
</head>
<body>

<section class="card card-contact">
  <div class="brand">
    <span class="brand-dot"></span>
    <span class="brand-name">Brightloom</span>
  </div>
  <h1 class="contact-name">Perry Dunmore</h1>
  <p class="contact-title">Founder &amp; CEO</p>
  <div class="contact-rule"></div>
  <ul class="contact-list">
    <li>
      <svg viewBox="0 0 24 24"><path d="M6.6 10.8a15.1 15.1 0 0 0 6.6 6.6l2.2-2.2c.3-.3.7-.4 1-.2 1.1.4 2.3.6 3.6.6.6 0 1 .4 1 1V20c0 .6-.4 1-1 1A17 17 0 0 1 3 4c0-.6.4-1 1-1h3.5c.6 0 1 .4 1 1 0 1.3.2 2.5.6 3.6.1.3 0 .7-.2 1z"/></svg>
      <span>(555)-014-2286</span>
    </li>
    <li>
      <svg viewBox="0 0 24 24"><path d="M2 5h20v14H2z M2 5l10 8 10-8" fill="none" stroke="#3b3b3b" stroke-width="2"/></svg>
      <span>pdunmore@quillpost-mail.net</span>
    </li>
  </ul>
</section>

<section class="card card-product">
  <div class="pattern-field" role="img" aria-label="Repeating pattern of the product symbol in soft teal and lilac"></div>
  <div class="product-block">
    <div class="product-mark">
      <span class="product-dot"></span>
      <span class="product-name">Glimworld</span>
    </div>
    <p class="product-tagline">Culturally Immersive Language Learning Games</p>
    <div class="product-web">
      <svg viewBox="0 0 110 10"><line x1="0" y1="5" x2="104" y2="5" stroke="#1f5fd6" stroke-width="1.2"/><circle cx="105" cy="5" r="3.5" fill="none" stroke="#1f5fd6" stroke-width="1.2"/></svg>
      <span class="product-url">www.glimworld-play.com</span>
      <svg viewBox="0 0 110 10"><circle cx="5" cy="5" r="3.5" fill="none" stroke="#1f5fd6" stroke-width="1.2"/><line x1="6" y1="5" x2="110" y2="5" stroke="#1f5fd6" stroke-width="1.2"/></svg>
    </div>
  </div>
</section>

</body>
</html>
```